New business card/stationary for a consulting company

I am looking for a clean and very professional looking business card for my consulting company as well as corresponding stationary. I am uploading our logo. I like simple and powerful for the feel. No graphics but I am open on everything else. Below is my contact information but would like the final to be in a version I can add my employees information into and print. Thank you.

Daniel Whitcombe
dan@ferncliffadvisory.com
2870 North 9th Avenue, Summit Floor, Elm Ridge, Illinois 60531
www.ferncliffadvisory.com

Industry/Entity Type

Consulting

Contact Information for Business Card

Daniel Whitcombe
dan@ferncliffadvisory.com
www.ferncliffadvisory.com

Font styles to use
Serif
Sans Serif

Requirements
Must have
• Our logo and the business card details.
Nice to have
• our website www.ferncliffadvisory.com

```html
<!DOCTYPE html>
<html lang="en">
<head>
<meta charset="utf-8">
<title>Ferncliff Advisory — Business Card</title>
<link rel="stylesheet" href="https://fonts.googleapis.com/css2?family=Cinzel:wght@400;700&family=Montserrat:wght@400&display=swap">
<style>
  :root {
    --navy: #2e2b6c;
    --ink: #2b2b2b;
    --muted: #4a4a4a;
    --rule: #b9b9b9;
    --paper: #ffffff;
    --backdrop: #e8e8ea;
  }
  * { box-sizing: border-box; margin: 0; padding: 0; }
  html, body {
    width: 1200px; height: 1200px; overflow: hidden;
    background: var(--backdrop);
  }
  .canvas {
    width: 1200px; height: 1200px;
    display: flex; align-items: center; justify-content: center;
  }
  .card {
    position: relative;
    width: 1000px; height: 668px;
    background: var(--paper);
    box-shadow: 0 2px 6px rgba(0,0,0,0.12);
    overflow: hidden;
  }
  .card__top-band {
    position: absolute; left: 0; top: 0;
    width: 100%; height: 35px;
    background: var(--navy);
  }
  .brand {
    position: absolute; right: 24px; top: 80px;
    display: flex; flex-direction: column; align-items: flex-end; gap: 18px;
  }
  .brand__mark {
    width: 48px; height: 48px;
    background: var(--navy);
    margin-right: 110px;
  }
  .brand__name {
    font-family: "Montserrat", sans-serif;
    font-weight: 400;
    font-size: 25px;
    letter-spacing: 0.5px;
    color: var(--navy);
    text-transform: uppercase;
  }
  .person {
    position: absolute; right: 628px; top: 300px;
    font-family: "Cinzel", serif;
    font-weight: 700;
    font-size: 41px;
    line-height: 58px;
    color: var(--ink);
    text-align: right;
    letter-spacing: 1px;
  }
  .divider {
    position: absolute; left: 407px; top: 290px;
    width: 2px; height: 130px;
    background: var(--rule);
  }
  .contact {
    position: absolute; left: 446px; top: 314px;
    list-style: none;
    font-family: "Montserrat", sans-serif;
    font-size: 21px;
    color: var(--muted);
    text-transform: uppercase;
    letter-spacing: 0.6px;
  }
  .contact__item {
    display: flex; align-items: center; gap: 16px;
    height: 42px;
  }
  .contact__icon { width: 22px; height: 22px; flex: none; }
  .address-band {
    position: absolute; left: 35px; right: 0; bottom: 25px;
    height: 62px;
    background: var(--navy);
    border-radius: 14px 0 0 14px;
    display: flex; align-items: center; gap: 6px;
    padding-left: 14px;
    font-family: "Cinzel", serif;
    font-weight: 400;
    font-size: 21px;
    color: var(--paper);
    letter-spacing: 0.4px;
  }
  .address-band__pin { width: 22px; height: 28px; flex: none; }
</style>
</head>
<body>
<main class="canvas">
  <article class="card">
    <div class="card__top-band"></div>

    <header class="brand">
      <div class="brand__mark"></div>
      <div class="brand__name">Ferncliff Advisory</div>
    </header>

    <h1 class="person">Daniel<br>Whitcombe</h1>

    <div class="divider"></div>

    <ul class="contact">
      <li class="contact__item">
        <svg class="contact__icon" viewBox="0 0 22 22" aria-hidden="true">
          <rect x="2" y="5" width="18" height="13" rx="2" fill="#3a3a3a"/>
          <path d="M3 6.5 L11 12.5 L19 6.5" fill="none" stroke="#ffffff" stroke-width="1.6"/>
        </svg>
        <span>dan@ferncliffadvisory.com</span>
      </li>
      <li class="contact__item">
        <svg class="contact__icon" viewBox="0 0 22 22" aria-hidden="true">
          <circle cx="11" cy="11" r="8" fill="#3a3a3a"/>
          <ellipse cx="11" cy="11" rx="3.5" ry="8" fill="none" stroke="#ffffff" stroke-width="1"/>
          <line x1="3" y1="11" x2="19" y2="11" stroke="#ffffff" stroke-width="1"/>
        </svg>
        <span>www.ferncliffadvisory.com</span>
      </li>
    </ul>

    <footer class="address-band">
      <svg class="address-band__pin" viewBox="0 0 22 28" aria-hidden="true">
        <path d="M11 2 C6 2 3 5.5 3 10 C3 16 11 25 11 25 C11 25 19 16 19 10 C19 5.5 16 2 11 2 Z" fill="#ffffff"/>
        <circle cx="11" cy="10" r="3.2" fill="#2e2b6c"/>
      </svg>
      <span>2870 North 9th Avenue, Summit Floor, Elm Ridge, Illinois 60531</span>
    </footer>
  </article>
</main>
</body>
</html>
```